New Business Card Design for Manufacturing

We are an engineering/manufacturing company that offers Advanced machining/assembly/engineering services, as well as innovative products for the heavy duty engine cooling markets.

We are looking to get a new business card designed that is clean and modern looking, but still fits the wide range of technical/skilled work we do.

- We hope to use this design as the base for other design work in new Presentations, web, and print work.

Industry/Entity Type

Engineering

Contact Information for Business Card

Our preferred color of blue is (RGB) 22/71/159 but can vary slightly from that color. Our content will be our Logo and full company name (Vantrell Forge Works, Inc.), company address, name, job title, phone number with extension, cell number, fax number, website, and email address on the cards.
We'd like the full company name next to the logo, but we are open to other interpretations of that layout.
Preferably, we would like the back side to be clean with just our logo, and the front to contain all of the contact information.

Colors
2f74b4
0355a3
85abd2

Requirements
Must have
• - Logo, company name, needed content - We are open to interpretation beyond that.
• - Standard size business card.
• - Horizontal orientation.
• - Enough space for lengthy names / job titles (for example, a job title could read "Directory of Human Resources" or "V.P. of Governmental Affairs"). We need this to look clean, whether the title be short (CEO) or long (as described above).

```html
<!DOCTYPE html>
<html lang="en">
<head>
<meta charset="utf-8">
<title>Vantrell Forge Works – Business Card</title>
<link rel="stylesheet" href="https://fonts.googleapis.com/css2?family=Open+Sans:wght@400;600;700&display=swap">
<style>
  :root {
    --brand-blue: #0d4b98;
    --brand-blue-dark: #0a3f84;
    --card-white: #f3f3f3;
    --text-grey: #6b6b6b;
    --rule-grey: #8a8a8a;
    --page-bg: #d9dbe0;
  }
  * { box-sizing: border-box; margin: 0; padding: 0; }
  html, body {
    width: 1200px; height: 900px; overflow: hidden;
    background: var(--page-bg);
    font-family: "Open Sans", Arial, sans-serif;
  }
  .sheet {
    position: relative; width: 1200px; height: 900px;
  }
  .card {
    position: absolute; left: 250px; width: 700px; height: 400px;
    box-shadow: 0 8px 24px rgba(0,0,0,0.18);
  }
  .card--back {
    top: 40px;
    background: linear-gradient(135deg, var(--brand-blue) 0%, var(--brand-blue-dark) 100%);
    display: flex; align-items: center; justify-content: center;
  }
  .card--front {
    top: 460px;
    background: linear-gradient(135deg, #e9e9e9 0%, var(--card-white) 60%, #ececec 100%);
  }
  .wordmark {
    display: flex; align-items: center; gap: 12px;
    font-weight: 700; letter-spacing: 0.5px;
  }
  .wordmark__square { width: 22px; height: 22px; }
  .card--back .wordmark { color: #ffffff; font-size: 32px; }
  .card--back .wordmark__square { background: #ffffff; }
  .card--front .wordmark {
    position: absolute; top: 78px; left: 0; right: 0; justify-content: center;
    color: var(--brand-blue); font-size: 40px;
  }
  .card--front .wordmark__square { background: var(--brand-blue); width: 28px; height: 28px; }
  .identity {
    position: absolute; right: 380px; top: 240px; text-align: right;
  }
  .identity__name {
    color: var(--brand-blue); font-weight: 600; font-size: 28px; line-height: 1.2;
  }
  .identity__title {
    color: var(--text-grey); font-size: 19px; line-height: 1.3;
  }
  .divider {
    position: absolute; left: 340px; top: 225px; width: 1.5px; height: 128px;
    background: var(--rule-grey);
  }
  .contact {
    position: absolute; left: 356px; top: 222px;
    color: var(--text-grey); font-size: 19px; line-height: 27px;
    list-style: none;
  }
  .contact__item { display: flex; align-items: center; gap: 10px; }
  .contact__item--address { padding-left: 4px; }
  .contact__icon { width: 16px; height: 16px; flex: none; }
</style>
</head>
<body>
<main class="sheet">
  <section class="card card--back" aria-label="Card back">
    <div class="wordmark"><span class="wordmark__square"></span>Vantrell Forge Works</div>
  </section>

  <section class="card card--front" aria-label="Card front">
    <div class="wordmark"><span class="wordmark__square"></span>Vantrell Forge Works</div>

    <div class="identity">
      <p class="identity__name">Dana Whitlow</p>
      <p class="identity__title">V.P. of Governmental Affairs</p>
    </div>

    <div class="divider"></div>

    <ul class="contact">
      <li class="contact__item contact__item--address">41 Millrace Lane</li>
      <li class="contact__item contact__item--address">Harlow Point, CA 93210.</li>
      <li class="contact__item">
        <svg class="contact__icon" viewBox="0 0 16 16" aria-hidden="true">
          <path d="M3.5 1.5l2.5 0 1 3.5-1.8 1.2c.8 1.8 2.2 3.2 4 4l1.2-1.8 3.5 1v2.5c0 .8-.7 1.5-1.5 1.5C7 13.4 2.6 9 2 3c0-.8.7-1.5 1.5-1.5z" fill="var(--brand-blue)"/>
        </svg>+1 555 014 2287</li>
      <li class="contact__item">
        <svg class="contact__icon" viewBox="0 0 16 16" aria-hidden="true">
          <rect x="1" y="3" width="14" height="10" rx="1" fill="var(--brand-blue)"/>
          <path d="M1.5 3.5L8 9l6.5-5.5" fill="none" stroke="#fff" stroke-width="1.3"/>
        </svg>hello@vantrellforge.com</li>
      <li class="contact__item">
        <svg class="contact__icon" viewBox="0 0 16 16" aria-hidden="true">
          <circle cx="8" cy="8" r="7" fill="var(--brand-blue)"/>
          <g fill="none" stroke="#fff" stroke-width="0.9">
            <ellipse cx="8" cy="8" rx="3" ry="7"/>
            <path d="M1 8h14M2 4.5h12M2 11.5h12"/>
          </g>
        </svg>www.vantrellforge.com</li>
    </ul>
  </section>
</main>
</body>
</html>
```